Marketing - Outdoor Vinyl banner, Outdoor Poster, Flyer modifications

Hi, I worked with you in the past and attached flyer designs. It just needs to be tweaked for various prints.
1)Outdoor vinyl banner (4 feet height and 8 feet width) print: Just grand opening pic, logo with name, tagline and call/text us portion.
2)Outdoor Poster (5 feet height and 3 feet width) print: same as above
3) Indoor poster for both horizontal & Vertical prints: Just logo w/ name, tagline, "We are MOVING Next door"
4)Flyer: will give minor modifications to attached flyer designs

```html
<!DOCTYPE html>
<html lang="en">
<head>
<meta charset="utf-8">
<title>Brightbay Dental – We are Moving Next Door</title>
<link rel="stylesheet" href="https://fonts.googleapis.com/css2?family=Montserrat:wght@400;500;600;700&display=swap">
<style>
  :root {
    --navy: #2d3f57;
    --cyan: #1cb1de;
    --white: #ffffff;
    --sky-edge: #7fd3ef;
  }
  * { margin: 0; padding: 0; box-sizing: border-box; }
  html, body {
    width: 849px;
    height: 1200px;
    overflow: hidden;
    background: var(--navy);
  }
  .poster {
    position: relative;
    width: 849px;
    height: 1200px;
    background: var(--navy);
    font-family: "Montserrat", Arial, sans-serif;
    color: var(--white);
    overflow: hidden;
  }
  .brand {
    position: absolute;
    top: 124px;
    left: 0;
    width: 100%;
    display: flex;
    justify-content: center;
    align-items: center;
    gap: 20px;
  }
  .brand-dot {
    width: 58px;
    height: 58px;
    border-radius: 50%;
    background: var(--cyan);
  }
  .brand-name {
    font-weight: 600;
    font-size: 52px;
    letter-spacing: 4px;
    color: var(--cyan);
    text-transform: uppercase;
  }
  .headline {
    position: absolute;
    top: 345px;
    left: 0;
    width: 100%;
    text-align: center;
  }
  .headline-top {
    font-weight: 500;
    font-size: 130px;
    line-height: 1;
    letter-spacing: -2px;
  }
  .headline-highlight-row {
    margin-top: 30px;
    height: 168px;
  }
  .headline-highlight {
    display: inline-block;
    padding: 0 18px;
    background: var(--cyan);
    font-weight: 700;
    font-size: 136px;
    line-height: 168px;
    letter-spacing: -1px;
    text-transform: uppercase;
    white-space: nowrap;
  }
  .headline-bottom {
    margin-top: 14px;
    font-weight: 500;
    font-size: 128px;
    line-height: 1;
    letter-spacing: -2px;
  }
  .footer-wave {
    position: absolute;
    left: 0;
    top: 870px;
    width: 849px;
    height: 330px;
  }
  .tagline {
    position: absolute;
    top: 1078px;
    left: 0;
    width: 100%;
    text-align: center;
    font-weight: 500;
    font-size: 52px;
    color: var(--cyan);
  }
  .tagline-strong {
    color: var(--navy);
  }
</style>
</head>
<body>
  <main class="poster">
    <header class="brand">
      <span class="brand-dot"></span>
      <span class="brand-name">Brightbay Dental</span>
    </header>

    <section class="headline">
      <p class="headline-top">We are</p>
      <p class="headline-highlight-row"><span class="headline-highlight">Moving</span></p>
      <p class="headline-bottom">Next door!</p>
    </section>

    <svg class="footer-wave" viewBox="0 0 849 330" preserveAspectRatio="none" aria-hidden="true">
      <path d="M0 40 C 250 130, 520 80, 849 20 L849 330 L0 330 Z" fill="var(--sky-edge)"/>
      <path d="M0 56 C 250 146, 520 96, 849 36 L849 330 L0 330 Z" fill="var(--cyan)"/>
      <path d="M0 70 C 250 160, 520 110, 849 50 L849 330 L0 330 Z" fill="var(--white)"/>
    </svg>

    <p class="tagline">Exicted to find <span class="tagline-strong">HOME!</span></p>
  </main>
</body>
</html>
```